Book cover

I need a cover for a my 3rd book that kinda goes with my brand (my previous book. The name of my first book - "Turbulence Behind the Yoke" Hidden Strain Inside Modern Cockpits: A Guide for Travelers". In the same style I need my third book - NO HARBOR" to stand out. I need a bolder, less whimsy cover, less playful. So can we use some of the same elements to stay consistent in this book cover. Perhaps use text to envoke emotions. This is the back cover so far (see below attachemnent)

Hello,
Subject: Cover Direction & Brand Consistency

Hi everyone,

Here’s my honest take: I don’t think the current execution fully reflects my brand yet. What I’m wondering is whether we can bring more continuity across my books—borrowing elements from my first and second covers to inform this third one. Think of how authors like Dorian Welk maintain a recognizable style across their work. That consistency builds trust and signals authority before a reader even opens the book. Design choices like this matter more than we realize.

I’ve attached a cover I came across on Brindlemart that reminded me of Option 5 and feels aligned with where you’re headed. One thought: could we experiment with introducing a crack—or cracks—into the word HARBOR itself? Maybe put the title "NO HARBOR" at the edge of the cover vertically?

Curious to hear your thoughts and how you see this evolving.
P.s. Is there away to attach an idea?

NO HARBOR: Restoring Quiet Edges in a Culture that Praises Hurry

```html
<!DOCTYPE html>
<html lang="en">
<head>
<meta charset="utf-8">
<title>No Harbor – Book Cover</title>
<link rel="stylesheet" href="https://fonts.googleapis.com/css2?family=Cinzel:wght@500;600&family=Montserrat:wght@300;400;600&family=Roboto:wght@400&family=Roboto+Condensed:wght@400&display=swap">
<style>
  :root {
    --page: #ffffff;
    --navy-top: #1a2432;
    --navy-bottom: #0c1016;
    --teal: #14b3b0;
    --pink: #f0508c;
    --magenta: #e85ad8;
    --white: #ffffff;
    --text-light: #f2f4f7;
    --sky-rose: #dd7a7a;
    --sky-peach: #d8906a;
    --sky-amber: #c98a4e;
    --dusk: #3b3a44;
    --ground: #161b24;
  }
  * { margin: 0; padding: 0; box-sizing: border-box; }
  html, body { width: 1200px; height: 1200px; overflow: hidden; background: var(--page); }
  .canvas { position: relative; width: 1200px; height: 1200px; }
  .cover { position: absolute; left: 28px; top: 180px; width: 1144px; height: 840px; display: flex; }

  .back-cover {
    position: relative; width: 571px; height: 100%;
    background: linear-gradient(180deg, var(--navy-top) 0%, #141b25 60%, var(--navy-bottom) 100%);
    color: var(--text-light); font-family: "Roboto", sans-serif;
  }
  .back-tagline {
    position: absolute; left: 54px; width: 466px; top: 63px;
    color: var(--teal); font-size: 13.6px; line-height: 16.8px; text-align: center;
  }
  .back-blurb {
    position: absolute; left: 54px; width: 466px; top: 132px;
    font-size: 13.6px; line-height: 16.85px; text-align: justify;
  }
  .back-blurb p { margin: 0; }
  .author-photo { position: absolute; left: 238px; top: 506px; width: 104px; height: 104px; }
  .author-bio {
    position: absolute; left: 54px; width: 466px; top: 619px;
    font-size: 13.6px; line-height: 16.85px; text-align: justify;
  }
  .logo-placeholder {
    position: absolute; left: 54px; top: 690px; width: 58px; height: 58px;
    background: linear-gradient(135deg, #1b8fc4, #0eb0b0);
  }
  .logo-label {
    position: absolute; left: 54px; top: 753px;
    font-family: "Roboto Condensed", sans-serif; font-size: 13.5px; line-height: 16px;
  }
  .series-note {
    position: absolute; left: 134px; top: 692px; width: 300px;
    font-size: 12.8px; line-height: 16.8px;
  }
  .series-note .trademark { color: var(--pink); display: block; margin-top: 3px; }
  .price {
    position: absolute; left: 452px; top: 744px;
    font-family: "Roboto Condensed", sans-serif; font-size: 17.5px; line-height: 22px;
  }

  .front-cover { position: relative; width: 573px; height: 100%; overflow: hidden; }
  .cover-photo {
    position: absolute; inset: 0;
    background: linear-gradient(180deg, var(--sky-rose) 0%, var(--sky-peach) 25%, var(--sky-amber) 42%, #8a6a55 60%, var(--dusk) 75%, var(--ground) 88%, #12161d 100%);
  }
  .title {
    position: absolute; left: 0; width: 573px; top: 118px; text-align: center;
    font-family: "Cinzel", serif; font-weight: 500; font-size: 78px; line-height: 1;
    color: var(--white); letter-spacing: 1px;
  }
  .subtitle {
    position: absolute; left: 63px; top: 214px; padding-left: 14px;
    border-left: 1.5px solid rgba(255,255,255,0.9);
    font-family: "Montserrat", sans-serif; font-weight: 300; font-size: 27px; line-height: 33.5px;
    color: var(--white); text-transform: uppercase;
  }
  .edition {
    position: absolute; left: 0; width: 573px; top: 690px; text-align: center;
    font-family: "Roboto", sans-serif; font-size: 20px; letter-spacing: 0.6px; color: var(--white);
  }
  .featuring {
    position: absolute; left: 0; width: 573px; top: 720px; text-align: center;
    font-family: "Roboto", sans-serif; font-size: 18px; color: var(--magenta);
  }
  .author-name {
    position: absolute; left: 0; width: 573px; top: 780px; text-align: center;
    font-family: "Montserrat", sans-serif; font-weight: 600; font-size: 16px; color: var(--white);
  }
  sup { font-size: 0.5em; }
</style>
</head>
<body>
<div class="canvas">
  <div class="cover">
    <section class="back-cover">
      <p class="back-tagline">Women have been told we could do and be anything … and we can.<br>What’s rarely mentioned is the toll on our health, relationships, and overall wellbeing.</p>
      <div class="back-blurb">
        <p>Are you the woman who holds it all together—crushing deadlines, leading teams, raising a family—while quietly unraveling inside? Yes, you are competent and capable. You’ve simply been carrying more than you were ever meant to for too long.</p>
        <p>No Harbor offers a different way forward. Drawn from decades of experience flying commercial aircraft and championing women's health, retired Captain Maren Lisswell reveals the missing skill most high-achieving women were never taught: protecting your margins in a world that glorifies overload. This vital buffer not only enables recovery after near-collapse, but also prevents you from reaching the breaking point of exhaustion.</p>
        <p>You will learn about the centuries-old mindset when humans first became cogs in the machine, the science of burnout and brain rewiring, the psychology driving us to push limits, and the cultural systems rigged against women. Discover how to spot the three stages of depletion before they ground you. Through self-assessment tools and actionable practices, the author guides us back home to ourselves by offering a roadmap to rebuild our strength, reconnect with joy and purpose, and redefine success to include true wellbeing.</p>
        <p>You don’t need to crash to earn a soft landing. Buckle up! No Harbor is your wakeup call to fly lighter and higher than you ever imagined.</p>
      </div>
      <svg class="author-photo" viewBox="0 0 104 104" role="img" aria-label="Portrait of the author in pilot uniform beside an aircraft engine">
        <defs>
          <linearGradient id="ring" x1="0" y1="1" x2="1" y2="0">
            <stop offset="0" stop-color="#1f6fd0"/>
            <stop offset="1" stop-color="#12b3b8"/>
          </linearGradient>
          <linearGradient id="portrait" x1="0" y1="0" x2="0" y2="1">
            <stop offset="0" stop-color="#8a8d94"/>
            <stop offset="1" stop-color="#2a2f3c"/>
          </linearGradient>
        </defs>
        <circle cx="52" cy="52" r="50" fill="url(#ring)"/>
        <circle cx="52" cy="52" r="46" fill="url(#portrait)"/>
      </svg>
      <p class="author-bio">Maren Lisswell is a speaker, consultant, and founder of the Skyward Balance Institute. With over 10,000 flight hours, she now empowers women to successfully lead without losing themselves.</p>
      <div class="logo-placeholder"></div>
      <p class="logo-label">SAMPLE<br>LOGO HERE</p>
      <p class="series-note">Part of the Quiet Margin Method Series.<sup>™</sup>
        <span class="trademark">The Quiet Margin Method is a trademark of Maren Lisswell.</span></p>
      <p class="price">US $99.99<br>CA $99.99</p>
    </section>

    <section class="front-cover">
      <div class="cover-photo" role="img" aria-label="Photograph of a jumbo jet taking off from a runway under a pink and orange sunset sky"></div>
      <h1 class="title">No Harbor</h1>
      <p class="subtitle">Restoring quiet edges<br>in a culture that<br>praises hurry</p>
      <p class="edition">REVISED &amp; EXPANDED EDITION</p>
      <p class="featuring">Featuring The Quiet Margin Method<sup>™</sup></p>
      <p class="author-name">CAPT. MAREN LISSWELL</p>
    </section>
  </div>
</div>
</body>
</html>
```